Quill Physical Therapy Website

I would need a clean modern website built to showcase my Physical therapy brand and services. I would need a simple but descriptive website that can ultimately connect my patients to my electronic medical portal so they may book an appointment..

```html
<!DOCTYPE html>
<html lang="en">
<head>
<meta charset="utf-8">
<title>Quill Physical Therapy &amp; Wellness</title>
<link href="https://fonts.googleapis.com/css2?family=Montserrat:ital,wght@0,300;0,400;0,500;0,600;0,700;0,800;1,400&family=Raleway:wght@400;500&display=swap" rel="stylesheet">
<style>
:root{
  --teal:#138a7b;
  --teal-dark:#0f7468;
  --green:#86c74e;
  --green-soft:#8fc95a;
  --violet:#5b6bbe;
  --ink:#222;
  --muted:#666;
  --mist:#edf4f3;
  --white:#fff;
}
*{box-sizing:border-box;margin:0;padding:0}
html,body{width:1200px;height:4313px;overflow:hidden}
body{font-family:"Raleway",sans-serif;color:var(--ink);background:var(--white);position:relative}
.abs{position:absolute}
section,header,footer{position:absolute;left:0;width:1200px;overflow:hidden}
.eyebrow{font-family:"Montserrat",sans-serif;font-size:15px;letter-spacing:3px;color:var(--green)}
.btn-outline{position:absolute;border:2px solid var(--teal);border-radius:30px;color:var(--teal);font:700 15px "Montserrat",sans-serif;letter-spacing:1px;display:flex;align-items:center;justify-content:center}
.btn-fill{position:absolute;background:var(--green);border-radius:30px;color:#fff;font:700 13px "Montserrat",sans-serif;letter-spacing:1px;display:flex;align-items:center;justify-content:center}
.rule{position:absolute;height:4px;width:40px;background:var(--green)}

/* header */
.site-header{top:0;height:109px;background:#fff;z-index:3}
.topbar{position:absolute;left:640px;top:0;width:560px;height:34px;background:var(--teal);border-bottom-left-radius:30px;color:#fff;font:500 12px "Montserrat",sans-serif;display:flex;align-items:center;gap:30px;padding-left:35px}
.topbar span{display:flex;align-items:center;gap:8px}
.topbar i{width:22px;height:22px;border-radius:50%;background:var(--green);display:inline-flex;align-items:center;justify-content:center}
.brand{position:absolute;left:110px;top:16px;display:flex;align-items:center;gap:10px}
.brand-dot{width:58px;height:58px;border-radius:50%;border:3px solid var(--teal)}
.brand-name{font:800 36px "Montserrat",sans-serif;color:var(--teal);line-height:1}
.brand-sub{font:600 7px "Montserrat",sans-serif;color:var(--green);letter-spacing:.5px;margin-top:3px}
.nav a{position:absolute;top:64px;font:500 12px "Montserrat",sans-serif;color:#333;text-decoration:none}
.nav a.active{color:var(--teal)}
.nav .underline{position:absolute;left:369px;top:92px;width:48px;height:3px;background:var(--green)}

/* hero */
.hero{top:109px;height:614px}
.hero-photo{position:absolute;inset:0;background:linear-gradient(100deg,#f1f2f2 0%,#eceeee 40%,#d9dcdc 62%,#c8cdd0 80%,#e0e2e2 100%)}
.hero .welcome{left:122px;top:138px;font:500 20px "Montserrat",sans-serif;letter-spacing:3px;color:#222}
.hero h1{position:absolute;left:115px;top:170px;font:800 50px "Montserrat",sans-serif;color:var(--teal);letter-spacing:1px}
.hero h2{position:absolute;left:115px;top:232px;font:400 35px "Montserrat",sans-serif;color:var(--green);letter-spacing:1px}
.hero .btn-fill{left:115px;top:293px;width:245px;height:47px;font-size:14px}
.hero .arrow{left:26px;top:200px}

/* offer */
.offer{top:723px;height:558px;background:#fff}
.offer-ring{position:absolute;left:151px;top:67px;width:418px;height:418px;border-radius:50%;border:3px solid var(--teal)}
.offer-photo{position:absolute;left:163px;top:79px;width:394px;height:394px;border-radius:50%;background:radial-gradient(circle at 55% 45%,#d9d6d0,#e9ecef 60%,#cfd6dc)}
.offer .eyebrow{position:absolute;left:641px;top:110px}
.offer .t1{position:absolute;left:638px;top:132px;font:400 46px "Montserrat",sans-serif;color:#333}
.offer .t2{position:absolute;left:638px;top:186px;font:800 46px "Montserrat",sans-serif;color:var(--teal);line-height:56px}
.offer .rule{left:648px;top:302px}
.offer p{position:absolute;left:648px;top:325px;width:440px;font-size:15px;line-height:29px;color:#444}
.offer .btn-outline{left:645px;top:404px;width:182px;height:50px}

/* services */
.services{top:1281px;height:554px;background:var(--violet)}
.services-bg{position:absolute;inset:0;background:linear-gradient(180deg,#5b6bbe 0%,#5868bc 60%,#6272bf 100%)}
.services .eyebrow{position:absolute;left:0;width:100%;top:46px;text-align:center;color:#fff}
.services h2{position:absolute;left:0;width:100%;top:68px;text-align:center;font:300 40px "Montserrat",sans-serif;color:#fff}
.services h2 b{font-weight:700}
.services .rule{left:580px;top:118px}
.card{position:absolute;top:167px;width:224px;height:288px;background:#fff;border:4px solid #fff;box-shadow:0 2px 6px rgba(0,0,0,.15);text-align:center}
.card .ph{height:188px}
.card .icon{position:absolute;left:75px;top:155px;width:66px;height:66px;border-radius:50%;background:var(--teal);border:3px solid #fff;display:flex;align-items:center;justify-content:center}
.card h3{position:absolute;left:0;width:100%;top:226px;font:700 15px "Montserrat",sans-serif;color:#333}
.card .caption{position:absolute;left:0;width:100%;top:252px;display:block;font-size:11px;color:#888;text-align:center;white-space:nowrap}

/* portal */
.portal{top:1835px;height:527px;background:#fff}
.portal-green{position:absolute;left:735px;top:0;width:465px;height:527px;background:var(--green)}
.portal .eyebrow{position:absolute;left:139px;top:120px}
.portal h2{position:absolute;left:139px;top:143px;font:400 42px "Montserrat",sans-serif;color:#333}
.portal h2 b{font-weight:700;color:var(--teal)}
.portal p{position:absolute;left:142px;top:210px;width:400px;font-size:13px;line-height:27px;color:#555}
.portal .btn-outline{left:139px;top:351px;width:169px;height:46px;font-size:13px}
.laptop-screen{position:absolute;left:602px;top:90px;width:452px;height:298px;background:#2a2a2a;border-radius:12px;padding:12px}
.laptop-screen div{width:100%;height:100%;background:linear-gradient(90deg,#26c0b4 0 4%,#f4f6f6 4%)}
.laptop-base{position:absolute;left:547px;top:388px;width:562px;height:14px;background:linear-gradient(#555,#333);border-radius:0 0 40px 40px}

/* testimonials */
.reviews{top:2362px;height:477px;background:var(--mist)}
.reviews h2{position:absolute;left:0;width:100%;top:72px;text-align:center;font:400 36px "Montserrat",sans-serif;color:#333}
.reviews h2 b{font-weight:700;color:var(--teal)}
.reviews .rule{left:580px;top:120px}
.quote{position:absolute;top:169px;width:429px;height:233px;background:#fff}
.quote p{position:absolute;left:33px;top:36px;width:370px;font:italic 400 14px/27px "Montserrat",sans-serif;color:#555}
.quote .avatar{position:absolute;left:37px;top:166px;width:40px;height:40px;border-radius:50%;background:#d8c8bb}
.quote .who{position:absolute;left:90px;top:164px;font:600 13px "Montserrat",sans-serif;color:var(--teal)}
.quote .stars{position:absolute;left:90px;top:182px;color:#f5b400;font-size:17px;letter-spacing:1px}

/* blogs */
.blogs{top:2839px;height:546px;background:#fff}
.blogs h2{position:absolute;left:126px;top:70px;font:400 36px "Montserrat",sans-serif;color:#333}
.blogs h2 b{font-weight:700;color:var(--teal)}
.blogs .rule{left:126px;top:118px;background:var(--teal)}
.post{position:absolute;top:149px;width:302px;height:298px;border:1px solid #ddd;background:#fff}
.post .ph{height:187px}
.post .date{position:absolute;left:0;top:165px;background:var(--green);color:#fff;font:700 10px "Montserrat",sans-serif;padding:6px 14px}
.post h3{position:absolute;left:22px;top:213px;width:260px;font:700 13px/20px "Montserrat",sans-serif;color:#222}
.post a{position:absolute;left:22px;top:262px;font:700 10px "Montserrat",sans-serif;color:var(--teal);text-decoration:none}

/* appointment */
.booking{top:3385px;height:560px}
.booking-photo{position:absolute;inset:0;background:linear-gradient(90deg,#fff 0%,#fff 42%,#e6e8ea 60%,#c9ced3 78%,#e9e6e2 100%)}
.booking h2{position:absolute;left:121px;top:62px;font:400 32px "Montserrat",sans-serif;color:#333}
.booking h2 b{font-weight:700;color:var(--teal)}
.booking .rule{left:121px;top:108px;background:var(--teal)}
.field{position:absolute;left:119px;width:422px;height:39px;border:1px solid #ccc;background:#fff;font:600 11px "Montserrat",sans-serif;color:#333;padding:12px 20px}
.booking .btn-fill{left:119px;top:390px;width:154px;height:38px;font-size:12px}

/* footer */
.site-footer{top:3880px;height:433px}
.footer-wave{position:absolute;left:0;top:0}
.footer-body{position:absolute;left:0;top:46px;width:1200px;height:319px;background:var(--teal)}
.footer-brand{position:absolute;left:145px;top:125px;text-align:center;color:#fff}
.footer-brand .dot{width:70px;height:70px;border-radius:50%;border:4px solid #fff;margin:0 auto 14px}
.footer-brand .name{font:800 40px "Montserrat",sans-serif;line-height:1}
.footer-brand .sub{font:600 8px "Montserrat",sans-serif;margin-top:4px}
.col h4{position:absolute;top:118px;font:700 14px "Montserrat",sans-serif;color:#fff}
.col .rule{top:140px;width:34px;height:3px}
.col li{position:absolute;list-style:none;font-size:12px;color:#e8f4f2;white-space:nowrap}
.social{position:absolute;top:271px;width:30px;height:30px;border-radius:50%;border:2px solid #fff}
.copyright{position:absolute;left:0;top:365px;width:1200px;height:68px;background:var(--teal-dark);color:#cfe6e2;font-size:11px;display:flex;align-items:center;justify-content:center}
</style>
</head>
<body>

<header class="site-header">
  <div class="topbar">
    <span><i><svg width="12" height="12" viewBox="0 0 24 24"><path fill="#fff" d="M6.6 10.8a15 15 0 0 0 6.6 6.6l2.2-2.2c.3-.3.7-.4 1-.2 1.1.4 2.3.6 3.6.6.6 0 1 .4 1 1V20c0 .6-.4 1-1 1A17 17 0 0 1 3 4c0-.6.4-1 1-1h3.5c.6 0 1 .4 1 1 0 1.3.2 2.5.6 3.6.1.3 0 .7-.2 1z"/></svg></i>CALL US TODAY (555) 010 2468</span>
    <span><i><svg width="12" height="12" viewBox="0 0 24 24"><path fill="#fff" d="M3 5h18v14H3zm2 2v.5l7 4.5 7-4.5V7z"/></svg></i>hello@quilltherapy.example</span>
  </div>
  <div class="brand">
    <div class="brand-dot"></div>
    <div>
      <div class="brand-name">QUILL</div>
      <div class="brand-sub">PHYSICAL THERAPY &amp; WELLNESS</div>
    </div>
  </div>
  <nav class="nav">
    <a class="active" style="left:373px" href="#">HOME</a>
    <a style="left:453px" href="#">ABOUT US</a>
    <a style="left:557px" href="#">OUR SERVICES</a>
    <a style="left:688px" href="#">WHY CHOOSE US</a>
    <a style="left:835px" href="#">CONTACT US</a>
    <span class="underline"></span>
  </nav>
  <a class="btn-fill" style="left:966px;top:57px;width:112px;height:30px;font-size:11px">BOOK NOW</a>
</header>

<section class="hero">
  <div class="hero-photo" role="img" aria-label="Therapist guiding a man lifting a small dumbbell in a bright clinic"></div>
  <svg class="abs arrow" width="20" height="36" viewBox="0 0 20 36"><path d="M17 2 3 18l14 16" fill="none" stroke="#8a9fa6" stroke-width="4"/></svg>
  <svg class="abs" style="right:12px;top:200px" width="20" height="36" viewBox="0 0 20 36"><path d="M3 2l14 16L3 34" fill="none" stroke="#fff" stroke-width="4" opacity=".6"/></svg>
  <div class="abs welcome">WELCOME TO OUR WEBSITE</div>
  <h1>QUILL PHYSICAL</h1>
  <h2>THERAPY &amp; WELLNESS</h2>
  <a class="btn-fill">BOOK APPOINTMENT
    <svg width="22" height="10" viewBox="0 0 22 10" style="margin-left:4px"><path d="M0 5h20M15 1l5 4-5 4" fill="none" stroke="#fff" stroke-width="1.6"/></svg></a>
  <svg class="abs" style="left:0;top:534px" width="1200" height="80" viewBox="0 0 1200 80">
    <path d="M0 80V48C260 10 520 10 780 22S1100 30 1200 10V80Z" fill="#fff"/>
    <path d="M90 44C320 8 560 8 780 20S1100 26 1200 6" fill="none" stroke="var(--green)" stroke-width="8"/>
  </svg>
</section>

<section class="offer">
  <div class="offer-ring"></div>
  <div class="offer-photo" role="img" aria-label="Smiling senior man stretching his arm with a therapist"></div>
  <svg class="abs" style="left:235px;top:440px" width="260" height="60" viewBox="0 0 260 60">
    <path d="M5 30C70 8 150 10 255 30" fill="none" stroke="var(--green)" stroke-width="6"/>
    <path d="M15 40C90 22 170 24 250 42" fill="none" stroke="var(--teal)" stroke-width="3"/>
  </svg>
  <div class="eyebrow">OUR THERAPY CENTER</div>
  <div class="t1">GET 25% OFF</div>
  <div class="t2">ON YOUR FIRST<br>TREATEMENT</div>
  <span class="rule"></span>
  <p>Lorem Ipsum is simply dummy text of the printing and type-setting industry. Lorem Ipsum has been</p>
  <a class="btn-outline">BOOK NOW</a>
</section>

<section class="services">
  <div class="services-bg" role="img" aria-label="Soft violet tinted backdrop of a therapy session"></div>
  <div class="eyebrow">WHAT WE DO</div>
  <h2>SERVICE <b>PROVIDE</b></h2>
  <span class="rule"></span>

  <div class="card" style="left:126px">
    <div class="ph" role="img" aria-label="Therapist checking a patient's shoulder" style="background:linear-gradient(135deg,#c9d2d8,#e6e4e0)"></div>
    <div class="icon"><svg width="30" height="30" viewBox="0 0 30 30" fill="none" stroke="#fff" stroke-width="2"><circle cx="15" cy="7" r="4"/><path d="M7 26v-6a8 8 0 0 1 16 0v6"/></svg></div>
    <h3>Injury Pain Relief</h3><p class="caption">Donec convallis pede venenatis</p>
  </div>
  <div class="card" style="left:365px;top:169px">
    <div class="ph" role="img" aria-label="Therapist treating a patient lying on a table" style="background:linear-gradient(135deg,#dfe2e4,#c3ccd2)"></div>
    <div class="icon"><svg width="30" height="30" viewBox="0 0 30 30" fill="none" stroke="#fff" stroke-width="2"><circle cx="15" cy="7" r="4"/><path d="M6 18h18v6H6zM10 14h10"/></svg></div>
    <h3>Physical Therapy</h3><p class="caption">Donec convallis pede venenatis</p>
  </div>
  <div class="card" style="left:599px;top:169px">
    <div class="ph" role="img" aria-label="Hands giving a back massage" style="background:linear-gradient(135deg,#d7a98a,#f0d3bd)"></div>
    <div class="icon"><svg width="30" height="30" viewBox="0 0 30 30" fill="none" stroke="#fff" stroke-width="2"><path d="M15 26S4 19 4 11a6 6 0 0 1 11-3 6 6 0 0 1 11 3c0 8-11 15-11 15z"/></svg></div>
    <h3>Wellness Service</h3><p class="caption">Donec convallis pede venenatis</p>
  </div>
  <div class="card" style="left:832px">
    <div class="ph" role="img" aria-label="Patient's back with highlighted spine" style="background:linear-gradient(135deg,#c8ccd0,#e7a08f)"></div>
    <div class="icon"><svg width="30" height="30" viewBox="0 0 30 30" fill="none" stroke="#fff" stroke-width="2"><circle cx="15" cy="6" r="3"/><path d="M15 10v14M8 14h14M10 26l5-4 5 4"/></svg></div>
    <h3>Joint Pain Relief</h3><p class="caption">Donec convallis pede venenatis</p>
  </div>
</section>

<section class="portal">
  <div class="portal-green"></div>
  <div class="eyebrow">BOOK YOUR APPOINTMENT</div>
  <h2>MEDICAL <b>PORTAL</b></h2>
  <p>Lorem Ipsum is simply dummy text of the printing and typesetting industry. Lorem Ipsum has been the industry's standard dummy text ever since the 1500s, when an unknown printer took a galley of type and scrambled it to make a type specimen book.</p>
  <a class="btn-outline">BOOK NOW</a>
  <div class="laptop-screen"><div role="img" aria-label="Laptop showing the patient portal timeline dashboard"></div></div>
  <div class="laptop-base"></div>
</section>

<section class="reviews">
  <h2>WHAT <b>PEOPLE SAYS</b></h2>
  <span class="rule"></span>
  <div class="quote" style="left:161px">
    <p>Lorem ipsum dolor sit amet, consectetur adipiscing elit, sed do eiusmod tempor incididunt ut labore et dolore magna aliqua Ut enim ad minim veniam, quis nostrud exercitation ullamco laboris nisi ut al</p>
    <div class="avatar" role="img" aria-label="Reviewer portrait"></div>
    <div class="who">Nora Vale</div><div class="stars">★★★★★</div>
  </div>
  <div class="quote" style="left:614px">
    <p>Lorem ipsum dolor sit amet, consectetur adipiscing elit, sed do eiusmod tempor incididunt ut labore et dolore magna aliqua Ut enim ad minim veniam, quis nostrud exercitation ullamco laboris nisi ut al</p>
    <div class="avatar" role="img" aria-label="Reviewer portrait"></div>
    <div class="who">Lena Brook</div><div class="stars">★★★★★</div>
  </div>
</section>

<section class="blogs">
  <h2>RECENT <b>BLOGS</b></h2>
  <span class="rule"></span>
  <article class="post" style="left:126px">
    <div class="ph" role="img" aria-label="Hands on a back with a highlighted spine" style="background:linear-gradient(135deg,#f08a6a,#f3d2c2)"></div>
    <span class="date">28 MAY 2021</span>
    <h3>Lorem ipsum dolor sit amet, con-sectetur adipiscing elit sed do</h3>
    <a href="#">LEARN MORE →</a>
  </article>
  <article class="post" style="left:440px">
    <div class="ph" role="img" aria-label="Therapist helping a patient stretch a leg" style="background:linear-gradient(135deg,#bfc6cb,#e5e7e8)"></div>
    <span class="date">28 MAY 2021</span>
    <h3>Lorem ipsum dolor sit amet, con-sectetur adipiscing elit sed do</h3>
    <a href="#">LEARN MORE →</a>
  </article>
  <article class="post" style="left:755px">
    <div class="ph" role="img" aria-label="Relaxing head massage by candlelight" style="background:linear-gradient(135deg,#6e5a4a,#d9b595)"></div>
    <span class="date">28 MAY 2021</span>
    <h3>Lorem ipsum dolor sit amet, con-sectetur adipiscing elit sed do</h3>
    <a href="#">LEARN MORE →</a>
  </article>
</section>

<section class="booking">
  <div class="booking-photo" role="img" aria-label="Therapist massaging a seated man's shoulders"></div>
  <h2>BOOK YOUR <b>APPOINTMENT</b></h2>
  <span class="rule"></span>
  <div class="field" style="top:140px">Name*</div>
  <div class="field" style="top:192px">Email address*</div>
  <div class="field" style="top:243px">Phone*</div>
  <div class="field" style="top:295px;height:78px">Message</div>
  <a class="btn-fill">SUBMIT NOW</a>
</section>

<footer class="site-footer">
  <svg class="footer-wave" width="1200" height="50" viewBox="0 0 1200 50">
    <path d="M0 50V40C300 0 700 -5 1200 30V50Z" fill="var(--teal)"/>
    <path d="M0 40C300 0 700 -5 1200 30" fill="none" stroke="var(--green)" stroke-width="5"/>
  </svg>
  <div class="footer-body"></div>
  <div class="footer-brand">
    <div class="dot"></div>
    <div class="name">QUILL</div>
    <div class="sub">PHYSICAL THERAPY &amp; WELLNESS</div>
  </div>
  <div class="col">
    <h4 style="left:413px">QUICK LINKS</h4><span class="rule" style="left:413px"></span>
    <ul>
      <li style="left:417px;top:168px">Home</li>
      <li style="left:417px;top:196px">About Us</li>
      <li style="left:417px;top:223px">Our Services</li>
      <li style="left:417px;top:251px">New Products</li>
      <li style="left:417px;top:279px">Contact Us</li>
    </ul>
    <h4 style="left:609px">RESOURCES</h4><span class="rule" style="left:609px"></span>
    <ul>
      <li style="left:614px;top:168px">News</li>
      <li style="left:614px;top:196px">Testimonials</li>
      <li style="left:614px;top:223px">Privacy Policy</li>
      <li style="left:614px;top:251px">Terms &amp; Condition</li>
    </ul>
    <h4 style="left:827px">CONTACT US</h4><span class="rule" style="left:827px"></span>
    <ul>
      <li style="left:827px;top:169px"><svg width="11" height="14" viewBox="0 0 12 16" style="vertical-align:-2px;margin-right:8px"><path fill="#fff" d="M6 0a6 6 0 0 0-6 6c0 4.5 6 10 6 10s6-5.5 6-10a6 6 0 0 0-6-6zm0 8.5A2.5 2.5 0 1 1 6 3.5a2.5 2.5 0 0 1 0 5z"/></svg>Office Lindenfeld | Birchweg 14</li>
      <li style="left:849px;top:192px">Office Talwiese | Mühlenweg 8</li>
      <li style="left:827px;top:215px"><svg width="12" height="12" viewBox="0 0 24 24" style="vertical-align:-2px;margin-right:8px"><path fill="#fff" d="M6.6 10.8a15 15 0 0 0 6.6 6.6l2.2-2.2c.3-.3.7-.4 1-.2 1.1.4 2.3.6 3.6.6.6 0 1 .4 1 1V20c0 .6-.4 1-1 1A17 17 0 0 1 3 4c0-.6.4-1 1-1h3.5c.6 0 1 .4 1 1 0 1.3.2 2.5.6 3.6.1.3 0 .7-.2 1z"/></svg>Tel: (555) 010 7711</li>
      <li style="left:827px;top:239px"><svg width="12" height="10" viewBox="0 0 24 18" style="vertical-align:-1px;margin-right:8px"><path fill="#fff" d="M0 0h24v18H0zm2 2v.5l10 6.5 10-6.5V2z"/></svg>Email: info@quill.example</li>
    </ul>
    <span class="social" style="left:822px"></span>
    <span class="social" style="left:859px"></span>
    <span class="social" style="left:896px"></span>
    <span class="social" style="left:933px"></span>
  </div>
  <div class="copyright">© 2021 Quill | All Rights Reserved &nbsp;|&nbsp; Terms &amp; Condition</div>
</footer>

</body>
</html>
```